Contemporary new French wine brand needs logo and series of label design

to design a new contemporary logo and series of labels for a new French wine brand. We hope to attract not just current French wine drinkers but new ones who may appreciate a less traditional and more modern style.
Updates

Reason: we are wanting to extend the project for a few days more to receive more submissions since we had fewer designs submitted than we were expecting, maybe because of the holidays.

Target Market(s)

people who follow the arts community (eg. music, theatre, visual/video arts, dance) --- all mature ages.

Industry/Entity Type

French Wine

Requirements
Must have
• a clear, memorable treatment for the name MORIVAL with accompanying logo.
Nice to have
• embossing, matte/gloss refinement, tasteful foil stamping, coated stock for the whites to help the integrity of the paper in and out of ice buckets. A combo of say, three types of fonts; a semi custom font for the brand name Morival and maybe a script and one other.
Should not have
• not traditional French

```html
<!DOCTYPE html>
<html lang="en">
<head>
<meta charset="utf-8">
<title>Morival – Viognier label</title>
<link rel="stylesheet" href="https://fonts.googleapis.com/css2?family=Alegreya+Sans:wght@300;400&family=Cormorant+Garamond:wght@400&display=swap">
<style>
  :root {
    --backdrop: #f1eee6;
    --gold-light: #e8d85c;
    --gold: #cdb52a;
    --gold-deep: #a8911a;
    --ink: #0c0c09;
    --name-ink: #2b2918;
  }
  * { margin: 0; padding: 0; box-sizing: border-box; }
  html, body {
    width: 871px;
    height: 1200px;
    overflow: hidden;
    background: var(--backdrop);
  }
  .canvas {
    position: relative;
    width: 871px;
    height: 1200px;
  }
  .label {
    position: absolute;
    left: 46px;
    top: 220px;
    width: 780px;
    height: 760px;
    background: linear-gradient(180deg, var(--gold-light) 0%, var(--gold) 55%, var(--gold-deep) 100%);
    overflow: hidden;
  }
  .label__band {
    position: absolute;
    left: 0;
    right: 0;
    top: 330px;
    bottom: 0;
    background: var(--ink);
  }
  .label__frame {
    position: absolute;
    left: 30px;
    right: 30px;
    top: 30px;
    bottom: 40px;
    border: 4px solid var(--ink);
  }
  .label__frame-inner {
    position: absolute;
    left: 44px;
    right: 44px;
    top: 330px;
    bottom: 54px;
    border: 2px solid var(--gold);
    border-top: none;
  }
  .brand-mark {
    position: absolute;
    left: 50%;
    top: 120px;
    width: 34px;
    height: 34px;
    margin-left: -17px;
    background: var(--name-ink);
  }
  .brand-name {
    position: absolute;
    left: 0;
    right: 0;
    top: 232px;
    text-align: center;
    font-family: "Alegreya Sans", sans-serif;
    font-weight: 400;
    font-size: 112px;
    line-height: 1;
    color: var(--name-ink);
    letter-spacing: -1px;
  }
  .varietal {
    position: absolute;
    left: 0;
    right: 0;
    top: 455px;
    text-align: center;
    font-family: "Alegreya Sans", sans-serif;
    font-weight: 300;
    font-style: italic;
    font-size: 40px;
    letter-spacing: 10px;
    color: var(--gold-light);
  }
  .region {
    position: absolute;
    left: 0;
    right: 0;
    top: 640px;
    text-align: center;
    font-family: "Cormorant Garamond", serif;
    font-size: 34px;
    color: var(--gold-light);
  }
</style>
</head>
<body>
  <main class="canvas">
    <section class="label">
      <div class="label__band"></div>
      <div class="label__frame"></div>
      <div class="label__frame-inner"></div>
      <span class="brand-mark" aria-hidden="true"></span>
      <h1 class="brand-name">Morival</h1>
      <p class="varietal">Viognier</p>
      <p class="region">burgundy</p>
    </section>
  </main>
</body>
</html>
```